Business Card Design Project

New Business Card design for Vantroke Technology Ltd using new Logo and new Tagline for staffing company.

About us from our website - www.vantroke-example.com:

VanTroke is a leading and recognized Electronic Entertainment, Workforce Augmentation, and Project Management solutions provider with clients in Electronic Entertainment, Legal, Technology, Government and other verticals that range in size from start up organizations to Meridex 500 companies. VanTroke is certified as an 8(a) minority and woman owned enterprise, established in 1998.

Target Market(s)

Companies in Electronic Entertainment, Legal, Government and Technology

Industry/Entity Type

Business

Requirements
Must have
• Must include in small letters the following information on back:

Established in 1998
8(a)(w)(e), Cage #7KTR9, DUNS #415260387

Front should have the following:
Pavel Orrin
Vice President
5678 Bramwick Lane
Tollerby, TB 654321
555-301-4826 X 100
555-309-1175 Fax
555-301-4826 Toll Free
name@vantroke-example.com

Our Tagline: Connect • Collaborate • Achieve

```html
<!DOCTYPE html>
<html lang="en">
<head>
<meta charset="utf-8">
<title>Vantroke Technology Ltd – Business Card</title>
<link rel="stylesheet" href="https://fonts.googleapis.com/css2?family=Arimo:wght@400;700&display=swap">
<style>
  :root {
    --page-bg: #ffffff;
    --card-black: #000000;
    --brand-blue: #1560b0;
    --brand-white: #ffffff;
    --band-white: #ffffff;
    --card-radius: 18px;
  }
  * { box-sizing: border-box; margin: 0; padding: 0; }
  html, body {
    width: 1200px;
    height: 900px;
    overflow: hidden;
    background: var(--page-bg);
    font-family: "Arimo", Arial, sans-serif;
  }
  .canvas {
    position: relative;
    width: 1200px;
    height: 900px;
  }
  .card {
    position: absolute;
    width: 690px;
    height: 410px;
    background: var(--card-black);
    border-radius: var(--card-radius);
    overflow: hidden;
    box-shadow: 0 2px 8px rgba(0,0,0,0.25);
  }

  /* Front */
  .card--front { left: 28px; top: 40px; }
  .contact-name {
    position: absolute;
    left: 52px; top: 52px;
    color: var(--brand-blue);
    font-weight: 700;
    font-size: 30px;
    line-height: 1;
  }
  .contact-title {
    position: absolute;
    left: 52px; top: 86px;
    color: var(--brand-blue);
    font-weight: 700;
    font-size: 23px;
    line-height: 1;
  }
  .contact-details {
    position: absolute;
    left: 70px; top: 140px;
    color: var(--brand-blue);
    font-size: 18px;
    line-height: 23px;
    list-style: none;
  }
  .brand {
    position: absolute;
    display: flex;
    align-items: center;
    gap: 12px;
  }
  .brand__dot {
    border-radius: 50%;
    background: var(--brand-blue);
    flex: none;
  }
  .brand__name {
    color: var(--brand-white);
    font-weight: 700;
    line-height: 1;
  }
  .card--front .brand { right: 52px; top: 108px; }
  .card--front .brand__dot { width: 28px; height: 28px; }
  .card--front .brand__name { font-size: 50px; }

  .tagline-band {
    position: absolute;
    left: 0; right: 0; bottom: 0;
    height: 72px;
    background: var(--band-white);
    display: flex;
    justify-content: space-around;
    align-items: center;
    padding: 0 40px;
  }
  .tagline-band__word {
    color: var(--brand-blue);
    font-weight: 700;
    font-size: 24px;
  }

  /* Back */
  .card--back { left: 482px; top: 460px; }
  .card--back .brand {
    left: 0; right: 0; top: 120px;
    justify-content: center;
  }
  .card--back .brand__dot { width: 40px; height: 40px; }
  .card--back .brand__name { font-size: 76px; }
  .established {
    position: absolute;
    left: 0; right: 0; top: 272px;
    text-align: center;
    color: var(--brand-white);
    font-weight: 700;
    font-size: 19px;
  }
  .registration {
    position: absolute;
    left: 0; right: 0; top: 318px;
    text-align: center;
    color: var(--brand-white);
    font-size: 12px;
    line-height: 16px;
    list-style: none;
  }
</style>
</head>
<body>
<main class="canvas">
  <section class="card card--front" aria-label="Business card front">
    <h1 class="contact-name">Pavel Orrin</h1>
    <p class="contact-title">Vice President</p>
    <ul class="contact-details">
      <li>5678 Bramwick Lane</li>
      <li>Tollerby, TB 654321</li>
      <li>555-301-4826 X 100</li>
      <li>555-309-1175 Fax</li>
      <li>555-301-4826 Toll Free</li>
      <li>name@vantroke-example.com</li>
    </ul>
    <div class="brand">
      <span class="brand__dot"></span>
      <span class="brand__name">VanTroke</span>
    </div>
    <div class="tagline-band">
      <span class="tagline-band__word">Connect</span>
      <span class="tagline-band__word">Collaborate</span>
      <span class="tagline-band__word">Achieve</span>
    </div>
  </section>

  <section class="card card--back" aria-label="Business card back">
    <div class="brand">
      <span class="brand__dot"></span>
      <span class="brand__name">VanTroke</span>
    </div>
    <p class="established">Established in 1998</p>
    <ul class="registration">
      <li>8(a)(w)(e)</li>
      <li>Cage #7KTR9</li>
      <li>DUNS #415260387</li>
    </ul>
  </section>
</main>
</body>
</html>
```